The Korvane LLC Asset Classes

I'm looking for for two designs here to go into powerpoint and potentially as a standalone PDF. My company does wealth management.
Graphic Image #1
I break down the investment world into 4 broad categories
-Preservation
-Capital Markets
-Real Estate
-Alternatives
In each broad category, there are subcategories:
Preservation: cash, checking/savings accounts, money market accounts, CD's, and fixed annuities.
Capital Markets: Publicly traded stocks and bonds
Real Estate: single-family residence, retail, industrial, multifamily, and office
Alternatives: private equity, private credit, cryptocurrency, asset-backed loans, tax liens, oil & gas, litigation finance, and royalties
Graphic 2: Please see the bottom f page 1 of the Tessolin Decks PDF.
Just like in graphic one, you have 4 categories of the Capital Markets and their respective subcategories
Category 1: Domestic Stocks: Subcategories are Large, mid, and small size companies
Category 2: International Stocks: Subcategories are Large, Mid/Small and by region - Developed and Emerging
Category 3: Fixed Income: You have subcategories like corporate, municipal, government, domestic, international
Category 4: Alternatives: The subcategories are metals and real estate
---------------------
I'm looking to create a graphic (either pie chart, or a circle broken into parts or some other clever way to illustrate this) to clearly illustrate both of these universes in a clean, professional, slick manner.
Target Market(s)
Investors
Colors
Designer to choose colors to be used in the design.
Requirements
Must have
- Clean
- professional
- Easy to read
- Creative
- Visually appealling
Nice to have
- I have attached my logo and some marketing materials so you can get a feel of what I am doing. Maybe you can clean this up too!

```html
<!DOCTYPE html>
<html lang="en">
<head>
<meta charset="utf-8">
<title>Korvane LLC Asset Classes</title>
<link href="https://fonts.googleapis.com/css2?family=Montserrat:wght@400;500;700&display=swap" rel="stylesheet">
<style>
  :root{
    --slate:#6b8fae;
    --orange:#f79a28;
    --teal:#189c9c;
    --olive:#9c9a7a;
    --navy:#1a659c;
    --ink:#1f5a8a;
    --paper:#ffffff;
  }
  *{margin:0;padding:0;box-sizing:border-box}
  html,body{width:873px;height:1200px;overflow:hidden;background:var(--paper)}
  body{position:relative;font-family:"Montserrat",sans-serif}
  .sheet{position:absolute;left:0;width:873px;overflow:hidden}
  .sheet--classes{top:0;height:614px}
  .sheet--markets{top:614px;height:586px}

  .brand{position:absolute;display:flex;align-items:center;gap:10px;
    font-weight:700;font-size:28px;color:var(--ink);letter-spacing:.5px}
  .brand__dot{width:30px;height:30px;border-radius:50%;background:var(--navy)}
  .sheet--classes .brand{left:590px;top:32px}
  .sheet--markets .brand{left:606px;top:32px}

  .chevron{position:absolute;display:flex;align-items:center;justify-content:center;
    text-align:center;color:#fff;font-weight:400;line-height:1.3;padding:0 20px 0 26px;
    clip-path:polygon(0 0,calc(100% - 15px) 0,100% 50%,calc(100% - 15px) 100%,0 100%,15px 50%)}
  .sheet--classes .chevron{top:98px;height:65px;font-size:19px}
  .sheet--markets .chevron{top:96px;height:68px;font-size:20px}

  .tile{position:absolute;display:flex;align-items:center;justify-content:center;
    text-align:center;color:#fff;font-weight:700;line-height:1.25;padding:0 6px}
  .sheet--classes .tile{height:41px;width:177px;font-size:14px}
  .sheet--markets .tile{height:43px;width:194px;font-size:16px}
  .tile--light{font-weight:500}

  .is-slate{background:var(--slate)}
  .is-orange{background:var(--orange)}
  .is-teal{background:var(--teal)}
  .is-olive{background:var(--olive)}

  .band{position:absolute;left:0;width:873px;height:45px;background:var(--navy)}
  .ring{position:absolute;width:168px;height:168px;border-radius:50%;
    border:50px solid var(--slate)}
</style>
</head>
<body>

<section class="sheet sheet--classes">
  <div class="brand"><span class="brand__dot"></span>Korvane LLC</div>

  <div class="chevron is-slate" style="left:23px;width:202px">Preservation</div>
  <div class="chevron is-orange" style="left:210px;width:203px">Capital<br>Markets</div>
  <div class="chevron is-teal" style="left:398px;width:204px">Real Estate</div>
  <div class="chevron is-olive" style="left:586px;width:203px">Alternatives</div>

  <div class="tile is-slate" style="left:24px;top:172px">Cash</div>
  <div class="tile is-slate" style="left:24px;top:219px">Checking/Savings accounts</div>
  <div class="tile is-slate" style="left:24px;top:265px">Money market accounts</div>
  <div class="tile is-slate" style="left:24px;top:312px">CD's</div>
  <div class="tile is-slate" style="left:24px;top:358px">Fixed annuities</div>

  <div class="tile is-orange" style="left:212px;top:172px">Publicly traded stocks and bonds</div>

  <div class="tile is-teal" style="left:400px;top:172px">Single-family residence</div>
  <div class="tile is-teal" style="left:400px;top:219px">Retail</div>
  <div class="tile is-teal" style="left:400px;top:265px">Industrial</div>
  <div class="tile is-teal" style="left:400px;top:312px">Multifamily</div>
  <div class="tile is-teal" style="left:400px;top:358px">Office</div>

  <div class="tile is-olive" style="left:589px;top:172px">Private equity</div>
  <div class="tile is-olive" style="left:589px;top:219px">Private credit</div>
  <div class="tile is-olive" style="left:589px;top:265px">Cryptocurrency</div>
  <div class="tile is-olive" style="left:589px;top:312px">Asset-backed loans</div>
  <div class="tile is-olive" style="left:589px;top:358px">Tax liens</div>
  <div class="tile is-olive" style="left:589px;top:405px">Oil &amp; gas</div>
  <div class="tile is-olive" style="left:589px;top:452px">Litigation finance</div>
  <div class="tile is-olive" style="left:589px;top:498px">Royalties</div>

  <div class="band" style="top:569px"></div>
  <div class="ring" style="left:787px;top:484px"></div>
</section>

<section class="sheet sheet--markets">
  <div class="brand"><span class="brand__dot"></span>Korvane LLC</div>

  <div class="chevron is-slate" style="left:12px;width:222px">Domestic<br>Stocks</div>
  <div class="chevron is-orange" style="left:219px;width:224px">International<br>Stocks</div>
  <div class="chevron is-teal" style="left:426px;width:224px">Fixed Income</div>
  <div class="chevron is-olive" style="left:634px;width:223px">Alternatives</div>

  <div class="tile is-slate" style="left:14px;top:173px">Large size companies</div>
  <div class="tile is-slate" style="left:14px;top:222px">Mid size companies</div>
  <div class="tile is-slate" style="left:14px;top:271px">Small size companies</div>

  <div class="tile is-orange" style="left:222px;top:173px">Large</div>
  <div class="tile is-orange" style="left:222px;top:222px">Mid</div>
  <div class="tile is-orange" style="left:222px;top:271px">Small</div>
  <div class="tile is-orange tile--light" style="left:222px;top:320px">Developed regions</div>
  <div class="tile is-orange tile--light" style="left:222px;top:369px">Emerging regions</div>

  <div class="tile is-teal" style="left:430px;top:173px">Corporate</div>
  <div class="tile is-teal" style="left:430px;top:222px">Municipal</div>
  <div class="tile is-teal" style="left:430px;top:271px">Government</div>
  <div class="tile is-teal" style="left:430px;top:320px">Domestic</div>
  <div class="tile is-teal" style="left:430px;top:369px">International</div>

  <div class="tile is-olive" style="left:637px;top:173px">Metals</div>
  <div class="tile is-olive" style="left:637px;top:222px">Estate</div>

  <div class="band" style="top:541px"></div>
  <div class="ring" style="left:784px;top:457px"></div>
</section>

</body>
</html>
```